Card design for orthopaedic surgeons working as The Brightwater Joint Centre

Business cards, letterhead

Colors

Designer to choose colors to be used in the design.

Requirements
Must have
• Late addition.
• Cards letterhead must have logos of
• Crestmoor Lindell College of Surgeons
• Varenwood Bone Health Association
Nice to have
• Back of card to have space for appointment time to be added by hand and some blank space for writing incidental other notes.

```html
<!DOCTYPE html>
<html lang="en">
<head>
<meta charset="utf-8">
<title>The Brightwater Joint Centre – Business Card</title>
<link rel="stylesheet" href="https://fonts.googleapis.com/css2?family=Arimo:wght@700&family=Lato:wght@400&display=swap">
<style>
  :root {
    --page-bg: #e9ecef;
    --navy: #06304d;
    --sky: #2eaaf5;
    --accent-text: #35aef5;
    --white: #ffffff;
    --disc: #f4f5f6;
    --logo-ink: #0d3a5c;
  }
  * { box-sizing: border-box; margin: 0; padding: 0; }
  html, body {
    width: 1200px;
    height: 900px;
    overflow: hidden;
    background: var(--page-bg);
  }
  .card {
    position: absolute;
    left: 160px;
    top: 177px;
    width: 880px;
    height: 546px;
    background: var(--sky);
    overflow: hidden;
    box-shadow: 0 10px 30px rgba(0, 0, 0, 0.15);
  }
  .card__panel {
    position: absolute;
    left: 0;
    top: 0;
    width: 595px;
    height: 100%;
    background: var(--navy);
  }
  .holder__name {
    position: absolute;
    left: 50px;
    top: 60px;
    font-family: "Arimo", Arial, sans-serif;
    font-weight: 700;
    font-size: 30px;
    letter-spacing: 0.3px;
    color: var(--accent-text);
    text-transform: uppercase;
  }
  .holder__role {
    position: absolute;
    left: 52px;
    top: 97px;
    font-family: "Lato", sans-serif;
    font-size: 24px;
    color: var(--white);
  }
  .contact {
    position: absolute;
    left: 48px;
    top: 297px;
    list-style: none;
    font-family: "Lato", sans-serif;
    font-size: 24px;
    color: var(--white);
  }
  .contact__item {
    display: flex;
    align-items: center;
    height: 32.5px;
    white-space: nowrap;
  }
  .contact__icon {
    width: 18px;
    height: 18px;
    margin-right: 9px;
    flex: none;
  }
  .address {
    position: absolute;
    left: 53px;
    top: 419px;
    font-family: "Lato", sans-serif;
    font-size: 24px;
    line-height: 32px;
    color: var(--white);
    white-space: nowrap;
  }
  .logo-disc {
    position: absolute;
    left: 363px;
    top: 54px;
    width: 470px;
    height: 470px;
    border-radius: 50%;
    background: var(--disc);
    box-shadow: 0 2px 10px rgba(0, 0, 0, 0.12);
    display: flex;
    align-items: center;
    justify-content: center;
  }
  .logo-disc__name {
    font-family: "Lato", sans-serif;
    font-weight: 400;
    font-size: 30px;
    color: var(--logo-ink);
    white-space: nowrap;
  }
</style>
</head>
<body>
  <div class="card">
    <div class="card__panel"></div>

    <p class="holder__name">Marcus Ellery</p>
    <p class="holder__role">Managing Director</p>

    <ul class="contact">
      <li class="contact__item">
        <svg class="contact__icon" viewBox="0 0 18 18" aria-hidden="true">
          <path d="M2 6 Q9 1 16 6 L14 8 L12 6.5 L6 6.5 L4 8 Z" fill="var(--accent-text)"/>
          <rect x="4" y="8.5" width="10" height="7" rx="1" fill="var(--accent-text)"/>
          <circle cx="9" cy="12" r="1.8" fill="var(--navy)"/>
        </svg>
        03-9412 7780
      </li>
      <li class="contact__item">
        <svg class="contact__icon" viewBox="0 0 18 18" aria-hidden="true">
          <rect x="1" y="4" width="16" height="11" fill="var(--accent-text)"/>
          <path d="M1 4 L9 10.5 L17 4" fill="none" stroke="var(--navy)" stroke-width="1.4"/>
        </svg>
        care@bwjoint.com.au
      </li>
      <li class="contact__item">
        <svg class="contact__icon" viewBox="0 0 18 18" aria-hidden="true">
          <circle cx="9" cy="9" r="8" fill="var(--accent-text)"/>
          <path d="M5 5 Q8 6 7 9 Q5 10 6 13 M11 3.5 Q10 6 12.5 7 Q14.5 9 12 12" fill="none" stroke="var(--navy)" stroke-width="1.4"/>
        </svg>
        www.bwjoint.com.au
      </li>
    </ul>

    <p class="address">18 Harbourview Road,<br>Larkfield 2480, Australia</p>

    <div class="logo-disc">
      <span class="logo-disc__name">The Brightwater Joint Centre</span>
    </div>
  </div>
</body>
</html>
```